New business card/stationary for a consulting company

I am looking for a clean and very professional looking business card for my consulting company as well as corresponding stationary. I am uploading our logo. I like simple and powerful for the feel. No graphics but I am open on everything else. Below is my contact information but would like the final to be in a version I can add my employees information into and print. Thank you.

Daniel Whitcombe
dan@ferncliffadvisory.com
2870 North 9th Avenue, Summit Floor, Elm Ridge, Illinois 60531
www.ferncliffadvisory.com

Industry/Entity Type

Consulting

Contact Information for Business Card

Daniel Whitcombe
dan@ferncliffadvisory.com
www.ferncliffadvisory.com

Font styles to use
Serif
Sans Serif

Requirements
Must have
• Our logo and the business card details.
Nice to have
• our website www.ferncliffadvisory.com

```html
<!DOCTYPE html>
<html lang="en">
<head>
<meta charset="utf-8">
<title>Ferncliff Advisory – Business Card</title>
<link rel="stylesheet" href="https://fonts.googleapis.com/css2?family=Tenor+Sans&family=Montserrat:wght@700&family=Roboto:wght@400&display=swap">
<style>
  :root {
    --navy: #05055f;
    --paper: #f4f4f4;
    --backdrop: #e4e4e4;
    --ink-grey: #555555;
    --white: #ffffff;
    --silver: #d9d9d9;
  }
  html, body {
    margin: 0;
    width: 1200px;
    height: 960px;
    overflow: hidden;
    background: var(--backdrop);
  }
  .canvas { position: relative; width: 1200px; height: 960px; }

  .card { position: absolute; width: 600px; height: 343px; }

  /* Front */
  .card-front { left: 302px; top: 128px; background: var(--paper); }
  .rule-thick { position: absolute; left: 0; top: 1px; width: 100%; height: 10px; background: var(--navy); }
  .rule-thin  { position: absolute; left: 0; top: 14px; width: 100%; height: 3px; background: var(--navy); }
  .brand-square {
    position: absolute; left: 180px; top: 121px;
    width: 57px; height: 57px; background: var(--navy);
  }
  .company-name {
    position: absolute; left: 37px; top: 188px; margin: 0;
    font-family: "Tenor Sans", sans-serif; font-weight: 400;
    font-size: 28px; letter-spacing: 0.5px; color: var(--navy); white-space: nowrap;
  }
  .person-name {
    position: absolute; left: 40px; top: 233px; margin: 0;
    font-family: "Montserrat", sans-serif; font-weight: 700;
    font-size: 18px; letter-spacing: 1px; color: var(--navy); white-space: nowrap;
  }
  .contact {
    position: absolute; left: 41px; top: 268px; margin: 0;
    font-family: "Roboto", sans-serif; font-size: 14px; line-height: 20px;
    color: var(--ink-grey); white-space: nowrap;
  }

  /* Back */
  .card-back { left: 299px; top: 488px; background: var(--navy); }
  .back-brand {
    position: absolute; left: 0; top: 142px; width: 100%;
    display: flex; justify-content: center; align-items: center; gap: 16px;
  }
  .back-square { width: 30px; height: 30px; background: var(--silver); }
  .back-name {
    font-family: "Tenor Sans", sans-serif; font-size: 30px;
    letter-spacing: 1px; color: var(--white); white-space: nowrap;
  }
  .back-url {
    position: absolute; left: 0; top: 286px; width: 100%; text-align: center;
    font-family: "Tenor Sans", sans-serif; font-size: 12px; letter-spacing: 3px;
    color: var(--white);
  }
</style>
</head>
<body>
<main class="canvas">
  <section class="card card-front">
    <div class="rule-thick"></div>
    <div class="rule-thin"></div>
    <div class="brand-square"></div>
    <h1 class="company-name">FERNCLIFF ADVISORY</h1>
    <h2 class="person-name">DANIEL WHITCOMBE</h2>
    <p class="contact">2870 North 9th Avenue, Summit Floor, Elm Ridge, Illinois 60531<br>dan@ferncliffadvisory.com | www.ferncliffadvisory.com</p>
  </section>

  <section class="card card-back">
    <div class="back-brand">
      <span class="back-square"></span>
      <span class="back-name">FERNCLIFF ADVISORY</span>
    </div>
    <p class="back-url">WWW.FERNCLIFFADVISORY.COM</p>
  </section>
</main>
</body>
</html>
```